Vorlanta PowerPoint Template

I have a company called Vorlanta, LLC and my company logo is already designed. I need a PowerPoint template that I will be using to pitch potential investors and business partners. This should be a very professional-looking template that leverages the company logo colors and really pops. The company is an AI product research and development company.

```html
<!DOCTYPE html>
<html lang="en">
<head>
<meta charset="utf-8">
<title>Vorlanta Presentation Template</title>
<link href="https://fonts.googleapis.com/css2?family=Montserrat:wght@400;500;700;800&family=Roboto:ital,wght@0,400;0,500;0,700;1,400;1,700&display=swap" rel="stylesheet">
<style>
:root{
  --stage:#6b6b6b;
  --red:#e8101c;
  --red-deep:#8a0a10;
  --pink:#ee8d8f;
  --ink:#2f2f2f;
  --ink-soft:#3a3a3a;
  --grey:#a9a9a9;
  --white:#ffffff;
  --night:#0c0c11;
}
*{margin:0;padding:0;box-sizing:border-box}
html,body{width:1016px;height:1200px;overflow:hidden;background:var(--stage)}
body{position:relative;font-family:'Roboto',sans-serif;color:var(--ink)}
.slide{position:absolute;width:425px;height:239px;overflow:hidden;background:var(--white);box-shadow:0 4px 14px rgba(0,0,0,.35)}
.col-left{left:70px}.col-right{left:520px}
.row-1{top:79px}.row-2{top:346px}.row-3{top:614px}.row-4{top:881px}
.abs{position:absolute}

.brand{position:absolute;display:flex;align-items:center;gap:5px;font-family:'Montserrat',sans-serif;font-weight:700;letter-spacing:-.3px}
.brand-dot{width:19px;height:19px;border-radius:50%;background:var(--red);flex:none}
.brand-name{font-size:17px;color:var(--ink)}
.brand.on-dark .brand-name{color:#d9d9d9}
.brand.top-right{right:14px;top:21px}

.slide-title{position:absolute;left:28px;top:18px;font-family:'Montserrat',sans-serif;font-size:19.5px;font-weight:800;color:var(--ink);white-space:nowrap}
.slide-title span{color:var(--red);font-weight:500}

.footer-bar{position:absolute;left:23px;top:214px;width:353px;height:16px;border-radius:8px;background:var(--red);display:flex;align-items:center;justify-content:center;gap:7px;color:var(--white);font-size:5.6px}
.footer-bar .item{display:flex;align-items:center;gap:2px}
.footer-bar .sep{opacity:.8}
.footer-bar svg{width:6px;height:6px}
.page-num{position:absolute;left:383px;top:212px;width:19px;height:19px;border-radius:50%;border:1.5px solid var(--red);display:flex;align-items:center;justify-content:center}
.page-num span{width:12px;height:12px;border-radius:50%;background:var(--red);color:var(--white);font-size:4.6px;font-weight:700;display:flex;align-items:center;justify-content:center}

/* title slide */
.title-slide{background:var(--night)}
.title-slide .visual{position:absolute;left:0;top:0;width:260px;height:239px;background:radial-gradient(ellipse at 55% 45%,#1c2233 0%,#15121b 45%,var(--night) 80%)}
.title-slide .brand{left:268px;top:73px}
.title-slide .brand-dot{width:26px;height:26px}
.title-slide .brand-name{font-size:22px}
.hero{position:absolute;left:238px;width:180px;top:109px;text-align:center;font-family:'Montserrat',sans-serif;font-weight:800;font-size:16px;line-height:21px;color:var(--white)}
.hero em{font-style:normal;color:var(--red)}
.hero-date{position:absolute;left:238px;width:180px;top:161px;text-align:center;font-size:6.3px;color:var(--white)}

/* why choose us */
.feature-text{position:absolute;width:58px;text-align:center;font-size:4.4px;line-height:7.9px;color:var(--ink-soft)}
.feature-text b{display:block;font-size:5px;margin-bottom:2px;color:var(--ink)}

/* contents */
.toc-bg{position:absolute;inset:0;background:linear-gradient(160deg,#ffffff 30%,#f1f1f1 65%,#e6e6e6 100%)}
.toc-row{position:absolute;left:30px;width:336px;font-size:8.6px;color:#1f1f1f;display:flex;align-items:center}
.toc-row .label{width:215px}
.toc-row .rule{width:69px;height:.6px;background:#b9b9b9}
.toc-row .num{margin-left:auto}

/* marketing */
.body-copy{position:absolute;font-size:6.9px;line-height:12.4px;text-align:justify;color:var(--ink-soft)}
.legend{position:absolute;left:307px;width:100px;font-size:4.1px;line-height:7.1px;color:var(--ink-soft)}
.legend li{list-style:none;position:relative;padding-left:7px;text-align:justify}
.legend li::before{content:"";position:absolute;left:0;top:1.8px;width:4px;height:4px;border-radius:50%;background:var(--c)}

/* about */
.about-visual{position:absolute;left:238px;top:49px;width:154px;height:154px;border-radius:50%;background:radial-gradient(circle at 50% 45%,#ff4650 0%,#c4121b 35%,#6b060b 75%,#2a0204 100%);border:1px solid #444}

/* testimonials */
.quote{position:absolute;width:165px;text-align:justify;text-align-last:center;font-size:7.1px;line-height:11.8px;font-style:italic;color:var(--ink-soft)}
.quote-mark{position:absolute;width:165px;text-align:center;font-family:'Montserrat',sans-serif;font-weight:800;font-size:22px;color:var(--red);line-height:1}
.quote-author{position:absolute;width:165px;text-align:center;font-size:6.9px;font-style:italic}
.quote-author b{font-weight:700}

/* section divider */
.divider-slide{background:#050101}
.divider-slide .visual{position:absolute;inset:0;background:radial-gradient(circle at 66% 50%,#ff2b2b 0%,#b00d12 14%,#560507 34%,#220203 55%,#050101 78%)}
.divider-slide .brand{left:22px;top:23px}
.divider-box{position:absolute;left:102px;top:150px;width:323px;height:41px;background:var(--white);display:flex;align-items:center;padding-left:23px;font-family:'Montserrat',sans-serif;font-weight:800;font-size:26px;color:var(--ink);white-space:nowrap}
.divider-box span{color:var(--red);font-weight:500;margin-left:9px}

/* thank you */
.thanks-slide{background:linear-gradient(100deg,#1a0203 0%,#4a0407 45%,#b50d14 100%)}
.thanks-slide .brand{left:42px;top:46px}
.thanks-title{position:absolute;left:42px;top:83px;font-family:'Montserrat',sans-serif;font-weight:800;font-size:24px;color:var(--white)}
.contact{position:absolute;left:41px;display:flex;align-items:center;gap:9px;font-size:7.5px;color:var(--white)}
.contact.strong{font-weight:700;font-size:9px}
.contact .ico{width:16px;height:16px;border-radius:50%;border:1px solid var(--white);display:flex;align-items:center;justify-content:center}
.contact .ico.filled{background:var(--red)}
.contact svg{width:8px;height:8px}
.thanks-ring{position:absolute;left:208px;top:6px;width:214px;height:214px;border-radius:50%;border:2px solid var(--white);background:repeating-linear-gradient(0deg,rgba(255,255,255,.55) 0 1.5px,transparent 1.5px 7px)}
.thanks-visual{position:absolute;left:225px;top:23px;width:180px;height:180px;border-radius:50%;background:radial-gradient(circle at 50% 45%,#ff6a6a 0%,#d0101a 18%,#7a060b 50%,#3a0205 85%)}
</style>
</head>
<body>

<!-- Title -->
<section class="slide title-slide col-left row-1">
  <div class="visual" role="img" aria-label="Dark photographic portrait built from glowing red contour lines"></div>
  <div class="brand on-dark"><span class="brand-dot"></span><span class="brand-name">Vorlanta</span></div>
  <h1 class="hero">Accelerating the<br><em>Future with AI</em></h1>
  <p class="hero-date">JUNE 03,2025</p>
</section>

<!-- Why Choose Us -->
<section class="slide col-right row-1">
  <h2 class="slide-title">Why <span>Choose Us</span></h2>
  <div class="brand top-right"><span class="brand-dot"></span><span class="brand-name">Vorlanta</span></div>
  <svg class="abs" style="left:0;top:0" width="425" height="239" viewBox="0 0 425 239">
    <g fill="none" stroke-linecap="round">
      <!-- node 1 -->
      <path d="M94 93 A30 30 0 0 1 124 63" stroke="#777" stroke-width="4"/>
      <path d="M124 57 A36 36 0 0 1 155 72" stroke="#333" stroke-width=".8"/>
      <path d="M88 93 L88 115 Q88 127 76 127 L66 127" stroke="#333" stroke-width=".8"/>
      <path d="M84 99 L84 117" stroke="#333" stroke-width=".8"/>
      <!-- node 2 -->
      <path d="M253 63 A30 30 0 0 1 283 93" stroke="#777" stroke-width="4"/>
      <path d="M222 72 A36 36 0 0 1 253 57" stroke="#333" stroke-width=".8"/>
      <!-- node 3 -->
      <path d="M159 162 A30 30 0 0 0 189 192" stroke="#777" stroke-width="4"/>
      <path d="M189 198 A36 36 0 0 0 220 184" stroke="#333" stroke-width=".8"/>
      <!-- node 4 -->
      <path d="M318 192 A30 30 0 0 0 348 162" stroke="#777" stroke-width="4"/>
      <path d="M287 184 A36 36 0 0 0 318 198" stroke="#333" stroke-width=".8"/>
      <path d="M354 162 L354 140 Q354 127 366 127 L376 127" stroke="#333" stroke-width=".8"/>
      <path d="M358 156 L358 139" stroke="#333" stroke-width=".8"/>
    </g>
    <circle cx="63" cy="127" r="2.5" fill="#fff" stroke="#333" stroke-width=".8"/>
    <circle cx="379" cy="127" r="2.5" fill="#fff" stroke="#333" stroke-width=".8"/>
    <circle cx="124" cy="93" r="24" fill="var(--red)"/>
    <circle cx="253" cy="93" r="24" fill="#333"/>
    <circle cx="189" cy="162" r="24" fill="#333"/>
    <circle cx="318" cy="162" r="24" fill="var(--red)"/>
    <!-- hierarchy icon -->
    <g fill="#fff">
      <rect x="121" y="83" width="6" height="5"/><rect x="114" y="96" width="5" height="5"/><rect x="121.5" y="96" width="5" height="5"/><rect x="129" y="96" width="5" height="5"/>
      <rect x="123.5" y="88" width="1" height="4"/><rect x="116" y="91.5" width="16" height="1"/><rect x="116" y="91.5" width="1" height="4.5"/><rect x="131" y="91.5" width="1" height="4.5"/><rect x="123.5" y="91.5" width="1" height="4.5"/>
    </g>
    <!-- monitor icon -->
    <g fill="none" stroke="#fff" stroke-width="2"><rect x="245" y="85" width="16" height="11" rx="1"/></g>
    <rect x="250" y="97" width="6" height="3" fill="#fff"/><rect x="247" y="100" width="12" height="1.5" fill="#fff"/>
    <!-- tick icon -->
    <path d="M182 162 L187 167 L196 157" fill="none" stroke="#fff" stroke-width="2.6" stroke-linecap="round" stroke-linejoin="round"/>
    <!-- people icon -->
    <g fill="#fff">
      <circle cx="318" cy="156" r="3.2"/><path d="M312 168 Q312 161 318 161 Q324 161 324 168 Z"/>
      <circle cx="311" cy="158" r="2.3"/><path d="M307 166 Q307 161 311 161 Q313 161 313.5 162 Q311 164 311 166 Z"/>
      <circle cx="325" cy="158" r="2.3"/><path d="M329 166 Q329 161 325 161 Q323 161 322.5 162 Q325 164 325 166 Z"/>
    </g>
  </svg>
  <p class="feature-text" style="left:90px;top:121px"><b>Lorem ipsum</b>Sed ut perspiciatis unde omnis iste natus error sit voluptatem accusantium doloremque laudantium, totam rem aperiam, eaque ipsa quae ab illo inventore veritatis et quasi architecto beatae vitae dicta sunt</p>
  <p class="feature-text" style="left:159px;top:60px"><b>Lorem ipsum</b>Sed ut perspiciatis unde omnis iste natus error sit voluptatem accusantium doloremque laudantium, totam rem aperiam, eaque ipsa quae ab illo inventore veritatis et quasi architecto beatae vitae dicta sunt</p>
  <p class="feature-text" style="left:222px;top:121px"><b>Lorem ipsum</b>Sed ut perspiciatis unde omnis iste natus error sit voluptatem accusantium doloremque laudantium, totam rem aperiam, eaque ipsa quae ab illo inventore veritatis et quasi architecto beatae vitae dicta sunt</p>
  <p class="feature-text" style="left:291px;top:60px"><b>Lorem ipsum</b>Sed ut perspiciatis unde omnis iste natus error sit voluptatem accusantium doloremque laudantium, totam rem aperiam, eaque ipsa quae ab illo inventore veritatis et quasi architecto beatae vitae dicta sunt</p>
  <div class="footer-bar">
    <span class="item"><svg viewBox="0 0 10 10"><path d="M1 2 L4 1 L6 2 L9 1 L9 8 L6 9 L4 8 L1 9 Z" fill="none" stroke="#fff" stroke-width="1"/></svg>112,ed ut perspiciatis unde omnis iste nat</span><span class="sep">|</span>
    <span class="item"><svg viewBox="0 0 10 10"><path d="M2 1 L4 1 L5 3.5 L3.8 4.5 Q5 6.5 6 6.2 L7 5 L9 6 L9 8 Q5 9.5 1 3 Z" fill="#fff"/></svg>+1 888 888 8888</span><span class="sep">|</span>
    <span class="item"><svg viewBox="0 0 10 10"><rect x="1" y="2" width="8" height="6" fill="#fff"/><path d="M1 2 L5 5.5 L9 2" fill="none" stroke="#e8101c" stroke-width=".8"/></svg>info@vorlanta-labs.com</span>
  </div>
  <div class="page-num"><span>05</span></div>
</section>

<!-- Table of Contents -->
<section class="slide col-left row-2">
  <div class="toc-bg" role="img" aria-label="Light grey wavy wireframe grid background"></div>
  <h2 class="slide-title" style="left:30px">Table of <span>Contents</span></h2>
  <div class="brand top-right"><span class="brand-dot"></span><span class="brand-name">Vorlanta</span></div>
  <div class="toc-row" style="top:69px"><span class="label">Sed ut perspiciatis unde omnis iste natus</span><span class="rule"></span><span class="num">03</span></div>
  <div class="toc-row" style="top:92px"><span class="label">Error sit voluptatem accusantium doloremque</span><span class="rule"></span><span class="num">04</span></div>
  <div class="toc-row" style="top:115px"><span class="label">Laudantium, totam rem aperiam, eaque ipsa</span><span class="rule"></span><span class="num">05</span></div>
  <div class="toc-row" style="top:138px"><span class="label">Quae ab illo inventore veritatis et quasi</span><span class="rule"></span><span class="num">06</span></div>
  <div class="toc-row" style="top:161px"><span class="label">Architecto beatae vitae dictas</span><span class="rule"></span><span class="num">07</span></div>
  <div class="footer-bar">
    <span class="item"><svg viewBox="0 0 10 10"><path d="M1 2 L4 1 L6 2 L9 1 L9 8 L6 9 L4 8 L1 9 Z" fill="none" stroke="#fff" stroke-width="1"/></svg>112,ed ut perspiciatis unde omnis iste nat</span><span class="sep">|</span>
    <span class="item"><svg viewBox="0 0 10 10"><path d="M2 1 L4 1 L5 3.5 L3.8 4.5 Q5 6.5 6 6.2 L7 5 L9 6 L9 8 Q5 9.5 1 3 Z" fill="#fff"/></svg>+1 888 888 8888</span><span class="sep">|</span>
    <span class="item"><svg viewBox="0 0 10 10"><rect x="1" y="2" width="8" height="6" fill="#fff"/><path d="M1 2 L5 5.5 L9 2" fill="none" stroke="#e8101c" stroke-width=".8"/></svg>info@vorlanta-labs.com</span>
  </div>
  <div class="page-num"><span>02</span></div>
</section>

<!-- Marketing Strategy -->
<section class="slide col-right row-2">
  <h2 class="slide-title" style="left:29px">Marketing <span>Strategy</span></h2>
  <div class="brand top-right"><span class="brand-dot"></span><span class="brand-name">Vorlanta</span></div>
  <p class="body-copy" style="left:30px;top:51px;width:124px">Sed ut perspiciatis unde omnis iste natus error sit voluptatem accusantium doloremque laudantium, totam rem aperiam, eaque ipsa quae ab illo inventore veritatied ut perspiciatis unde omnis iste natus error sit voluptatem accusantium doloremque laudantium, totam rem aperiam, eaque ipsa quae ab illo inventore veritati et quasi architecto beatae vitae dicta sunt explicabo.</p>
  <svg class="abs" style="left:173px;top:66px" width="120" height="120" viewBox="-60 -60 120 120">
    <g stroke="#fff" stroke-width="2" stroke-linejoin="round">
      <path d="M0 0 L0 -60 A60 60 0 0 1 48.5 35.3 Z" fill="var(--red)"/>
      <path d="M0 0 L48.5 35.3 A60 60 0 0 1 -57.1 18.5 Z" fill="#333"/>
      <path d="M0 0 L-57.1 18.5 A60 60 0 0 1 -35.3 -48.5 Z" fill="var(--pink)"/>
      <path d="M0 0 L-35.3 -48.5 A60 60 0 0 1 0 -60 Z" fill="var(--grey)"/>
    </g>
    <g fill="#fff" font-family="Roboto,sans-serif" font-weight="700" font-size="5.5" text-anchor="middle">
      <text x="23" y="-22">35%</text><text x="27" y="28">35%</text><text x="-30" y="16">20%</text><text x="-17" y="-30">10%</text>
    </g>
  </svg>
  <ul class="legend" style="top:71px">
    <li style="--c:#333;margin-bottom:13px">Sed ut perspiciatis unde omnis iste natus error sit voluptatem a doloremque laudantium, totam rem aperiam, eaque ipsa quae ab illo inventore ve beatae vitae</li>
    <li style="--c:var(--red);margin-bottom:9px">Sed ut perspiciatis unde omnis iste natus error sit voluptatem a doloremque laudantium, totam rem aperiam, eaque ipsa</li>
    <li style="--c:var(--pink);margin-bottom:13px">Sed ut perspiciatis unde omnis iste natus error sit voluptatem a doloremque laudantium, totam rem aperiam, eaque ipsa quae ab illo inventore ve beatae vitae</li>
    <li style="--c:var(--grey)">Sed ut perspiciatis unde omnis iste natus error sit voluptatem a doloremque laudantium, totam rem aperiam, eaque ipsa</li>
  </ul>
  <div class="footer-bar">
    <span class="item"><svg viewBox="0 0 10 10"><path d="M1 2 L4 1 L6 2 L9 1 L9 8 L6 9 L4 8 L1 9 Z" fill="none" stroke="#fff" stroke-width="1"/></svg>112,ed ut perspiciatis unde omnis iste nat</span><span class="sep">|</span>
    <span class="item"><svg viewBox="0 0 10 10"><path d="M2 1 L4 1 L5 3.5 L3.8 4.5 Q5 6.5 6 6.2 L7 5 L9 6 L9 8 Q5 9.5 1 3 Z" fill="#fff"/></svg>+1 888 888 8888</span><span class="sep">|</span>
    <span class="item"><svg viewBox="0 0 10 10"><rect x="1" y="2" width="8" height="6" fill="#fff"/><path d="M1 2 L5 5.5 L9 2" fill="none" stroke="#e8101c" stroke-width=".8"/></svg>info@vorlanta-labs.com</span>
  </div>
  <div class="page-num"><span>06</span></div>
</section>

<!-- About Us -->
<section class="slide col-left row-3">
  <h2 class="slide-title" style="left:30px">About <span>Us</span></h2>
  <div class="brand top-right"><span class="brand-dot"></span><span class="brand-name">Vorlanta</span></div>
  <p class="body-copy" style="left:30px;top:56px;width:186px;line-height:11.6px;font-size:6.6px">Sed ut perspiciatis unde omnis iste natus error sit voluptatem accusantium doloremque laudantium, totam rem aperiam, eaque ipsa quae ab illo inventore veritatis et quasi architecto beatae vitae dicta sunt explicabo. Nemo enim ipsam voluptatem quia voluptas sit aspernatur aut odit aut fugit, sed quia consequuntur magni dolores eos qui ratione voluptatem sequi nesciunt. Neque porro quisquam est, qui dolorem ipsum quia dolor sit amet, consecteturSed ut perspiciatis unde omnis iste natus error sit voluptatem accusantium doloremque laudantium, totam rem aperiam, eaque ipsa quae ab illo inventore veritatis et quasi architecto beatae</p>
  <div class="about-visual" role="img" aria-label="Red glowing AI microchip in a circuit corridor"></div>
  <div class="footer-bar">
    <span class="item"><svg viewBox="0 0 10 10"><path d="M1 2 L4 1 L6 2 L9 1 L9 8 L6 9 L4 8 L1 9 Z" fill="none" stroke="#fff" stroke-width="1"/></svg>112,ed ut perspiciatis unde omnis iste nat</span><span class="sep">|</span>
    <span class="item"><svg viewBox="0 0 10 10"><path d="M2 1 L4 1 L5 3.5 L3.8 4.5 Q5 6.5 6 6.2 L7 5 L9 6 L9 8 Q5 9.5 1 3 Z" fill="#fff"/></svg>+1 888 888 8888</span><span class="sep">|</span>
    <span class="item"><svg viewBox="0 0 10 10"><rect x="1" y="2" width="8" height="6" fill="#fff"/><path d="M1 2 L5 5.5 L9 2" fill="none" stroke="#e8101c" stroke-width=".8"/></svg>info@vorlanta-labs.com</span>
  </div>
  <div class="page-num"><span>03</span></div>
</section>

<!-- Customer Testimonials -->
<section class="slide col-right row-3">
  <h2 class="slide-title" style="left:28px">Customer <span>Testimonials</span></h2>
  <div class="brand top-right"><span class="brand-dot"></span><span class="brand-name">Vorlanta</span></div>
  <div class="quote-mark" style="left:28px;top:64px">&ldquo;</div>
  <p class="quote" style="left:28px;top:83px">“Sed ut perspiciatis unde omnis iste natus error sit voluptatem accusantium doloremque laudantium, totam rem aperiam, eaque ipsa quae ab illo inventatis et quasi architecto beatae vitae dunt explic accusantium doloremque laudantium, totam rem aperiam, eaque ipsa quae ab illo inventatis et quasi architecto beatae vitae dunt explicabo.”</p>
  <p class="quote-author" style="left:28px;top:172px"><b>JOHN DOE</b>,Customer</p>
  <div class="quote-mark" style="left:232px;top:64px">&ldquo;</div>
  <p class="quote" style="left:232px;top:83px">“Sed ut perspiciatis unde omnis iste natus error sit voluptatem accusantium doloremque laudantium, totam rem aperiam, eaque ipsa quae ab illo inventatis et quasi architecto beatae vitae dunt explic accusantium doloremque laudantium, totam rem aperiam, eaque ipsa quae ab illo inventatis et quasi architecto beatae vitae dunt explicabo.”</p>
  <p class="quote-author" style="left:232px;top:172px"><b>JOHN DOE</b>,Customer</p>
  <div class="footer-bar">
    <span class="item"><svg viewBox="0 0 10 10"><path d="M1 2 L4 1 L6 2 L9 1 L9 8 L6 9 L4 8 L1 9 Z" fill="none" stroke="#fff" stroke-width="1"/></svg>112,ed ut perspiciatis unde omnis iste nat</span><span class="sep">|</span>
    <span class="item"><svg viewBox="0 0 10 10"><path d="M2 1 L4 1 L5 3.5 L3.8 4.5 Q5 6.5 6 6.2 L7 5 L9 6 L9 8 Q5 9.5 1 3 Z" fill="#fff"/></svg>+1 888 888 8888</span><span class="sep">|</span>
    <span class="item"><svg viewBox="0 0 10 10"><rect x="1" y="2" width="8" height="6" fill="#fff"/><path d="M1 2 L5 5.5 L9 2" fill="none" stroke="#e8101c" stroke-width=".8"/></svg>info@vorlanta-labs.com</span>
  </div>
  <div class="page-num"><span>07</span></div>
</section>

<!-- Section Divider -->
<section class="slide divider-slide col-left row-4">
  <div class="visual" role="img" aria-label="Abstract red particle streams radiating from a glowing centre"></div>
  <div class="brand on-dark"><span class="brand-dot"></span><span class="brand-name">Vorlanta</span></div>
  <h2 class="divider-box">Section<span>Divider Title</span></h2>
</section>

<!-- Thank You -->
<section class="slide thanks-slide col-right row-4">
  <div class="thanks-ring"></div>
  <div class="thanks-visual" role="img" aria-label="Hand touching a glowing red AI interface"></div>
  <div class="brand on-dark"><span class="brand-dot"></span><span class="brand-name">Vorlanta</span></div>
  <h2 class="thanks-title">THANK YOU</h2>
  <div class="contact" style="top:120px"><span class="ico"><svg viewBox="0 0 10 10"><path d="M1 2 L4 1 L6 2 L9 1 L9 8 L6 9 L4 8 L1 9 Z" fill="#fff"/></svg></span>112,ed ut perspiciatis unde omnis iste nat</div>
  <div class="contact strong" style="top:148px"><span class="ico filled"><svg viewBox="0 0 10 10"><path d="M2 1 L4 1 L5 3.5 L3.8 4.5 Q5 6.5 6 6.2 L7 5 L9 6 L9 8 Q5 9.5 1 3 Z" fill="#fff"/></svg></span>+1 888 888 8888</div>
  <div class="contact" style="top:177px"><span class="ico"><svg viewBox="0 0 10 10"><rect x="1" y="2" width="8" height="6" fill="#fff"/><path d="M1 2 L5 5.5 L9 2" fill="none" stroke="#4a0407" stroke-width=".8"/></svg></span>info@vorlanta-labs.com</div>
</section>

</body>
</html>
```